Zielgruppe
Immobilienmakler
Aufgabenstellung
Top moderne hochwertige Visitenkate, wir hätten gerne eine sehr hochwertig moderne Visitenkarte mit Bild vom Mitarbeiter... Anbei habe ich die alte Visitenkarte die ich sehr kindlich finde... Es sollte jetzt sehr exklusive aussehen. Alle Daten können von der alten Visitenkarte übernommen werden.. danke

```html
<!DOCTYPE html>
<html lang="de">
<head>
<meta charset="utf-8">
<title>Velta Agentur – Visitenkarte</title>
<link rel="stylesheet" href="https://fonts.googleapis.com/css2?family=Fira+Sans+Condensed:wght@400&family=Cinzel:wght@400&display=swap">
<style>
  :root {
    --stage: #ebecea;
    --label: #8f9191;
    --card: #ffffff;
    --band: #b8ccd9;
    --brand-light: #a9bfcf;
    --ink: #231f20;
    --green: #158a42;
    --emboss-hi: #ffffff;
    --emboss-lo: #d9dadb;
  }
  * { margin: 0; padding: 0; box-sizing: border-box; }
  html, body { width: 1200px; height: 614px; overflow: hidden; background: var(--stage); }
  body { position: relative; font-family: "Fira Sans Condensed", sans-serif; color: var(--ink); }

  .side-label {
    position: absolute; top: 68px; font-size: 25px; font-weight: 400;
    color: var(--label); letter-spacing: 0.5px; transform: translateX(-50%);
  }
  .side-label--front { left: 345px; }
  .side-label--back { left: 864px; }

  .finish-note {
    position: absolute; left: 521px; top: 151px; transform: translateX(-50%);
    font-size: 20px; color: var(--label); letter-spacing: 0.3px;
  }
  .finish-note__line {
    position: absolute; left: 521px; top: 178px; width: 1px; height: 29px; background: var(--label);
  }

  .card {
    position: absolute; top: 193px; width: 493px; height: 323px;
    background: var(--card); overflow: hidden;
  }
  .card--front { left: 88px; }
  .card--back { left: 617px; }

  /* Front */
  .card__footer-band { position: absolute; left: 0; right: 0; bottom: 0; height: 26px; background: var(--band); }
  .emboss { position: absolute; left: 405px; top: 27px; width: 56px; height: 56px; }
  .front-brand {
    position: absolute; right: 58px; top: 122px;
    font-family: "Cinzel", serif; font-size: 25px; font-weight: 400;
    color: var(--brand-light); letter-spacing: 1px; white-space: nowrap;
  }
  .front-tagline {
    position: absolute; right: 60px; top: 158px;
    font-family: "Cinzel", serif; font-size: 9px; letter-spacing: 0.6px; color: var(--ink);
  }

  /* Back */
  .card__header-band { position: absolute; left: 0; right: 0; top: 0; height: 105px; background: var(--band); }
  .back-brand {
    position: absolute; right: 56px; top: 38px;
    font-family: "Cinzel", serif; font-size: 36px; font-weight: 400;
    color: var(--ink); letter-spacing: 1.2px; line-height: 1; white-space: nowrap;
  }
  .back-tagline {
    position: absolute; left: 250px; top: 112px;
    font-family: "Cinzel", serif; font-size: 14px; letter-spacing: 0.9px; color: var(--ink);
  }
  .person { position: absolute; left: 249px; top: 142px; }
  .person__name { font-family: "Cinzel", serif; font-size: 23px; letter-spacing: 0.6px; line-height: 28px; }
  .person__role { font-size: 15px; color: var(--green); line-height: 17px; }

  .contact {
    position: absolute; right: 276px; top: 183px; text-align: right;
    font-size: 17px; line-height: 19.2px; list-style: none;
  }
  .contact__key { margin-right: 10px; }

  .portrait {
    position: absolute; left: 328px; top: 203px; width: 150px; height: 120px;
    background: linear-gradient(180deg, #f6f6f7 0%, #eceef1 55%, #dfe3e9 100%);
    border-radius: 60px 60px 0 0;
  }
</style>
</head>
<body>
  <div class="side-label side-label--front">VORDERSEITE</div>
  <div class="side-label side-label--back">RÜCKSEITE</div>

  <div class="finish-note">BLINDPRÄGUNG</div>
  <div class="finish-note__line"></div>

  <section class="card card--front" aria-label="Vorderseite">
    <svg class="emboss" viewBox="0 0 56 56" aria-hidden="true">
      <circle cx="28" cy="28" r="26" fill="none" stroke="var(--emboss-lo)" stroke-width="1.6"/>
      <circle cx="28" cy="28" r="26" fill="none" stroke="var(--emboss-hi)" stroke-width="1" transform="translate(-0.7 -0.7)"/>
    </svg>
    <div class="front-brand">Velta Agentur</div>
    <div class="front-tagline">DER IMMOBILIENMAKLER</div>
    <div class="card__footer-band"></div>
  </section>

  <section class="card card--back" aria-label="Rückseite">
    <div class="card__header-band"></div>
    <div class="back-brand">Velta Agentur</div>
    <div class="back-tagline">DER IMMOBILIENMAKLER</div>

    <div class="person">
      <div class="person__name">LUKAS BRENNER</div>
      <div class="person__role">Dipl. Immobilienmanager</div>
      <div class="person__role">Geschäftsführer</div>
    </div>

    <ul class="contact">
      <li>Am Rain 14</li>
      <li>6850 Dornbirn</li>
      <li><span class="contact__key">T</span>+43 5572 48 216 30</li>
      <li><span class="contact__key">M</span>+43 660 2847 519</li>
      <li>lukas@velta-agentur.com</li>
      <li>velta-agentur.com</li>
    </ul>

    <div class="portrait" role="img" aria-label="Porträtfoto des Mitarbeiters im weißen Hemd, Sakko über der Schulter"></div>
  </section>
</body>
</html>
```